Private practice for psychiatry and psychotherapy needs a business card and logo

I need a logo and business card design for my private practice for psychiatry and psychotherapy. The optional names for my practice are: Vorsteling Praktijk voor Psychiatrie en Psychotherapie, or short: Praktijk Vorsteling.
I am a (child and adolescent) psychiatrist and psychotherapist. I diagnose and treat infants, children, adolescents and adults with psychiatric symptoms/disorders. I also give supervision to colleagues about their own treatments. My work is characterised by personal involvement, transparence, creativity and professionality.
I would like to have an appealing, light and bright, yet basic design that invites people (both children and adults) to contact me, gives trust and hope, without loosing professional appearance.
I uploaded my contact information which should not necessarily be all included (in this form) on the card as long as people know how to contact me. Please feel free to be creative!
Please note that my website is only temporarely and need a new design and update too!

Target Market(s)

Clients and patients (children, adolescents, adults) with psychiatric symptoms who need diagnosis and treatment. I work with private clients and patients through medical insurances.

Industry/Entity Type

Mental Health

Contact Information for Business Card

Dr. Ilse Vorsteling-ter Haaf
Psychiater/Kinder- en Jeugdpsychiater
Jorisvan Heultstraat 14
3071 PW Rotterdam
t: 06-58190274
e: info@praktijkvorsteling.nl
i: www.praktijkvorsteling.nl

Logo Text

Praktijk Vorsteling voor Psychiatrie en Psychotherapie; or short: Praktijk Vorsteling

Font styles to use
Sans Serif
Other font styles liked:
• up to designer

Requirements
Must have
• Appealing, light, bright, creative, trustful, professional and unique.

```html
<!DOCTYPE html>
<html lang="nl">
<head>
<meta charset="utf-8">
<title>Praktijk Vorsteling – visitekaartje</title>
<link href="https://fonts.googleapis.com/css2?family=Montserrat:wght@600;700&family=Open+Sans:wght@400;600&display=swap" rel="stylesheet">
<style>
  :root {
    --bg: #1e1f21;
    --card: #2a2b2d;
    --card-edge: #333436;
    --silver: #a9abae;
    --white: #f2f2f2;
    --text: #d6d6d6;
    --blue: #2a8fd6;
    --divider: #7a7b7d;
  }
  * { margin: 0; padding: 0; box-sizing: border-box; }
  html, body { width: 1200px; height: 1000px; overflow: hidden; background: var(--bg); }
  .canvas {
    width: 1200px; height: 1000px;
    display: flex; flex-direction: column; align-items: center; justify-content: center; gap: 70px;
  }
  .card {
    width: 720px; height: 400px;
    background: var(--card);
    border: 1px solid var(--card-edge);
    box-shadow: 0 18px 40px rgba(0,0,0,.45);
    position: relative;
  }
  /* front */
  .card--front { display: flex; flex-direction: column; align-items: center; justify-content: center; gap: 22px; }
  .brand-dot { width: 72px; height: 72px; border-radius: 50%; background: var(--silver); }
  .brand-name {
    font-family: "Montserrat", sans-serif; font-weight: 700; font-size: 24px;
    letter-spacing: 1px; text-transform: uppercase; color: var(--silver);
  }
  /* back */
  .card--back { padding: 0 50px; }
  .back-main { display: flex; align-items: center; height: 300px; padding-top: 40px; }
  .back-brand { width: 240px; display: flex; flex-direction: column; align-items: center; gap: 16px; }
  .back-brand .brand-dot { width: 64px; height: 64px; background: var(--blue); }
  .back-brand .brand-name { color: var(--white); font-size: 17px; }
  .divider { width: 3px; height: 150px; background: var(--divider); margin: 0 28px 0 14px; }
  .contact { font-family: "Open Sans", sans-serif; color: var(--text); }
  .contact__name {
    font-family: "Montserrat", sans-serif; font-weight: 600; font-size: 21px;
    color: var(--white); text-transform: uppercase; letter-spacing: .3px;
  }
  .contact__role { font-weight: 600; font-size: 15px; color: var(--blue); margin: 2px 0 10px; }
  .contact__list { list-style: none; }
  .contact__list li { display: flex; align-items: center; gap: 16px; font-size: 17px; line-height: 27px; letter-spacing: .4px; }
  .contact__list svg { width: 15px; height: 15px; fill: var(--blue); flex: none; }
  .accent { color: var(--blue); }
  .address {
    display: flex; align-items: center; justify-content: center; gap: 16px;
    font-family: "Open Sans", sans-serif; font-size: 18px; letter-spacing: 1px; color: var(--text);
    padding-left: 70px;
  }
  .address svg { width: 16px; height: 20px; fill: var(--blue); }
</style>
</head>
<body>
<main class="canvas">
  <section class="card card--front">
    <div class="brand-dot"></div>
    <div class="brand-name">Praktijk Vorsteling</div>
  </section>

  <section class="card card--back">
    <div class="back-main">
      <div class="back-brand">
        <div class="brand-dot"></div>
        <div class="brand-name">Praktijk Vorsteling</div>
      </div>
      <div class="divider"></div>
      <div class="contact">
        <div class="contact__name">Dr. Ilse Vorsteling-ter Haaf</div>
        <div class="contact__role">Psychiater/Kinder- en Jeugdpsychiater</div>
        <ul class="contact__list">
          <li><svg viewBox="0 0 24 24"><path d="M6.6 10.8a15 15 0 0 0 6.6 6.6l2.2-2.2a1 1 0 0 1 1-.25 11.4 11.4 0 0 0 3.6.57 1 1 0 0 1 1 1V20a1 1 0 0 1-1 1A17 17 0 0 1 3 4a1 1 0 0 1 1-1h3.5a1 1 0 0 1 1 1c0 1.25.2 2.45.57 3.57a1 1 0 0 1-.25 1z"/></svg>06-58190274</li>
          <li><svg viewBox="0 0 24 24"><path d="M2 5h20v14H2z" opacity="0"/><path d="M2 5h20v2l-10 6L2 7zm0 4.3l10 6 10-6V19H2z"/></svg>info@praktijkvorsteling.nl</li>
          <li><svg viewBox="0 0 24 24"><path d="M12 2a10 10 0 1 0 0 20 10 10 0 0 0 0-20zm6.9 6h-3a15 15 0 0 0-1.3-3.9A8 8 0 0 1 18.9 8zM12 4c.8 1.2 1.5 2.5 1.9 4h-3.8c.4-1.5 1.1-2.8 1.9-4zM4.3 14a8 8 0 0 1 0-4h3.4a16 16 0 0 0 0 4zm.8 2h3a15 15 0 0 0 1.3 3.9A8 8 0 0 1 5.1 16zm3-8h-3a8 8 0 0 1 4.3-3.9A15 15 0 0 0 8.1 8zM12 20c-.8-1.2-1.5-2.5-1.9-4h3.8c-.4 1.5-1.1 2.8-1.9 4zm2.3-6H9.7a14 14 0 0 1 0-4h4.6a14 14 0 0 1 0 4zm.3 5.9a15 15 0 0 0 1.3-3.9h3a8 8 0 0 1-4.3 3.9zm1.7-5.9a16 16 0 0 0 0-4h3.4a8 8 0 0 1 0 4z"/></svg>www.<span class="accent">praktijkvorsteling</span>.nl</li>
        </ul>
      </div>
    </div>
    <div class="address">
      <svg viewBox="0 0 16 20"><path d="M8 0a8 8 0 0 0-8 8c0 6 8 12 8 12s8-6 8-12a8 8 0 0 0-8-8zm0 11a3 3 0 1 1 0-6 3 3 0 0 1 0 6z"/></svg>
      Jorisvan Heultstraat 14 3071 PW Rotterdam
    </div>
  </section>
</main>
</body>
</html>
```